KAJU Freightways #ALLKAJU Business Cards & Letterhead

I am looking to business cards designed for our organization. We are currently undergoing a small re-branding that is taking place. Our organization is called KAJU Freightways and we are headquartered in Phoenix, AZ. We primarily provide transportation and logistics services to the Marlow Parcel Bureau who is our largest customer. I would like to see a design that incorporates name, title, contact info, website, and address (this will be different depending on the employee). I would also like to see some color on the business card using our logo colors or a variation. I would like our logo on the back of the business card with the website displayed. The final design should communicate that we are a next generation transportation operate that focuses on being driver-first, customer-centric, innovative, and sustainable.We would also like our #ALLKAJU catch phrase incorporated as well.

Target Market(s)

Transportation & Logistics

Industry/Entity Type

Trucking Company

Contact Information for Business Card

-First and Last Name
-Position Title
-Contact Phone
-Contact Email
-Physical Address

Font styles to use
Serif

Colors

Designer to choose colors to be used in the design.

Requirements
Must have
• -KAJU logo prominently displayed
• -#ALLKAJU catch phrase used
• -Some amount of color, design gradient, etc.
• -Logo on the back with website listed (https://www.kajufreightco.example)

```html
<!DOCTYPE html>
<html lang="en">
<head>
<meta charset="utf-8">
<title>KAJU Freightways Business Card</title>
<link rel="stylesheet" href="https://fonts.googleapis.com/css2?family=Lora:wght@400;500;600;700&display=swap">
<style>
  :root {
    --stage: #2b2b2b;
    --card-white: #ffffff;
    --brand-teal: #123c48;
    --brand-green: #7dc242;
    --ink: #123c48;
  }
  * { box-sizing: border-box; margin: 0; padding: 0; }
  html, body { width: 1200px; height: 878px; overflow: hidden; }
  body {
    background: var(--stage);
    font-family: "Lora", serif;
    display: flex;
    flex-direction: column;
    align-items: center;
    justify-content: center;
    gap: 26px;
  }
  .card {
    width: 700px;
    height: 400px;
    border-radius: 26px;
    position: relative;
    overflow: hidden;
    box-shadow: 0 10px 24px rgba(0,0,0,0.45);
  }

  /* Back */
  .card-back { background: var(--brand-teal); }
  .card-back .brand {
    position: absolute;
    left: 50%; top: 42%;
    transform: translate(-50%, -50%);
    display: flex; align-items: center; gap: 18px;
  }
  .card-back .brand-ring {
    width: 46px; height: 46px;
    border: 6px solid var(--brand-green);
    border-radius: 50%;
  }
  .card-back .brand-name {
    color: var(--card-white);
    font-weight: 700;
    font-size: 76px;
    letter-spacing: 2px;
    line-height: 1;
  }
  .card-back .tagline {
    position: absolute;
    left: 0; right: 0; top: 232px;
    text-align: center;
    color: var(--brand-green);
    font-weight: 600;
    font-size: 20px;
    letter-spacing: 4px;
  }
  .card-back .website {
    position: absolute;
    left: 0; right: 0; bottom: 46px;
    text-align: center;
    color: var(--card-white);
    font-weight: 500;
    font-size: 19px;
    letter-spacing: 2px;
  }

  /* Front */
  .card-front { background: var(--card-white); }
  .card-front .brand {
    position: absolute;
    left: 30px; top: 50%;
    transform: translateY(-50%);
    width: 300px;
    display: flex; align-items: center; justify-content: center; gap: 14px;
  }
  .card-front .brand-ring {
    width: 40px; height: 40px;
    border: 6px solid var(--brand-green);
    border-radius: 50%;
  }
  .card-front .brand-name {
    color: var(--brand-teal);
    font-weight: 700;
    font-size: 68px;
    letter-spacing: 1px;
    line-height: 1;
  }
  .divider {
    position: absolute;
    left: 350px; top: 58px;
    width: 2px; height: 284px;
    background: var(--brand-green);
  }
  .details {
    position: absolute;
    left: 380px; top: 62px;
    right: 24px;
    color: var(--ink);
  }
  .person-name {
    color: var(--brand-green);
    font-weight: 600;
    font-size: 26px;
    letter-spacing: 1.5px;
    text-transform: uppercase;
    line-height: 1.15;
  }
  .person-title {
    font-size: 16px;
    letter-spacing: 1px;
    margin: 2px 0 16px;
  }
  .address {
    font-style: normal;
    font-size: 17px;
    line-height: 1.35;
    letter-spacing: 0.5px;
    margin-bottom: 14px;
  }
  .contact-list { list-style: none; font-size: 16px; letter-spacing: 0.5px; }
  .contact-list li { display: flex; align-items: center; gap: 10px; line-height: 1.55; white-space: nowrap; }
  .contact-list svg { width: 14px; height: 14px; flex: none; }
  .accent { color: var(--brand-green); }
</style>
</head>
<body>
  <section class="card card-back" aria-label="Card back">
    <div class="brand">
      <span class="brand-ring"></span>
      <span class="brand-name">KAJU</span>
    </div>
    <p class="tagline">#ALLKAJU</p>
    <p class="website">www.kajufreightco.example</p>
  </section>

  <section class="card card-front" aria-label="Card front">
    <div class="brand">
      <span class="brand-ring"></span>
      <span class="brand-name">KAJU</span>
    </div>
    <div class="divider"></div>
    <div class="details">
      <h1 class="person-name">Dana Whitfield</h1>
      <p class="person-title">Director</p>
      <address class="address">
        4170 North Cactus<br>
        Ridge Road<br>
        Glendale, AZ 85308
      </address>
      <ul class="contact-list">
        <li>
          <svg viewBox="0 0 24 24" aria-hidden="true"><path fill="#7dc242" d="M6.6 10.8a15.1 15.1 0 0 0 6.6 6.6l2.2-2.2a1 1 0 0 1 1-.25 11.4 11.4 0 0 0 3.6.57 1 1 0 0 1 1 1V20a1 1 0 0 1-1 1A17 17 0 0 1 3 4a1 1 0 0 1 1-1h3.5a1 1 0 0 1 1 1c0 1.25.2 2.45.57 3.57a1 1 0 0 1-.25 1z"/></svg>
          623-555-0148
        </li>
        <li>
          <svg viewBox="0 0 24 24" aria-hidden="true"><rect x="3" y="5" width="18" height="14" rx="2" fill="none" stroke="#7dc242" stroke-width="2"/><path d="M3 7l9 6 9-6" fill="none" stroke="#7dc242" stroke-width="2"/></svg>
          info@kajufreightco.example
        </li>
        <li>
          <svg viewBox="0 0 24 24" aria-hidden="true"><circle cx="12" cy="12" r="9" fill="none" stroke="#7dc242" stroke-width="2"/><path d="M3 12h18M12 3c3 3.5 3 14.5 0 18M12 3c-3 3.5-3 14.5 0 18" fill="none" stroke="#7dc242" stroke-width="1.6"/></svg>
          <span>www.<span class="accent">kajufreightco</span>.example</span>
        </li>
      </ul>
    </div>
  </section>
</body>
</html>
```